Business card for medical clinic

I need an upmarket, modern medical/health business card for my clinic

Contact Information for Business Card

name, address, email, qr code

```html
<!DOCTYPE html>
<html lang="en">
<head>
<meta charset="utf-8">
<title>Aurelis Care Partners — Business Card</title>
<link href="https://fonts.googleapis.com/css2?family=Montserrat:wght@400;500;600&display=swap" rel="stylesheet">
<style>
  :root {
    --canvas-bg: #d9d5cf;
    --card-navy: #1e2944;
    --accent-blue: #2aa3e2;
    --brand-blue: #1f7fae;
    --deep-mark: #2e3f86;
    --emboss-dark: #2a3a6e;
    --text-light: #eef1f6;
  }
  * { margin: 0; padding: 0; box-sizing: border-box; }
  html, body {
    width: 900px;
    height: 1200px;
    overflow: hidden;
  }
  body {
    position: relative;
    background: var(--canvas-bg);
    font-family: "Montserrat", Arial, sans-serif;
    color: var(--text-light);
  }
  .card {
    position: absolute;
    background: var(--card-navy);
    border-radius: 24px;
    overflow: hidden;
  }
  .card--front { left: 80px; top: 130px; width: 742px; height: 442px; }
  .card--back  { left: 78px; top: 638px; width: 744px; height: 440px; }

  .brand-name {
    position: absolute;
    font-weight: 500;
    letter-spacing: 1px;
    text-transform: uppercase;
    white-space: nowrap;
  }
  .card--front .brand-name {
    left: 34px; top: 44px;
    font-size: 24px;
    color: var(--brand-blue);
  }
  .card--back .brand-name {
    left: 206px; top: 212px;
    font-size: 32px;
    color: var(--emboss-dark);
  }

  .holder {
    position: absolute;
    right: 50px; top: 40px;
    text-align: right;
  }
  .holder__name {
    font-size: 25px;
    font-weight: 600;
    color: var(--accent-blue);
    line-height: 1.2;
  }
  .holder__role {
    font-size: 15px;
    font-weight: 500;
    margin-top: 4px;
  }

  .address {
    position: absolute;
    left: 41px; top: 250px;
    font-size: 16px;
    line-height: 20px;
  }
  .contacts {
    position: absolute;
    left: 41px; top: 327px;
    list-style: none;
  }
  .contacts li {
    display: flex;
    align-items: center;
    height: 22px;
    margin-bottom: 9.5px;
    font-size: 16px;
  }
  .contacts svg {
    width: 16px; height: 16px;
    margin-right: 10px;
    flex: none;
  }
  .decor-ring {
    position: absolute;
  }
  .card--front .decor-ring { left: 442px; top: 180px; }
  .card--back .decor-ring { left: 148px; top: 148px; }
</style>
</head>
<body>

<section class="card card--front">
  <div class="brand-name">Aurelis Care Partners</div>

  <div class="holder">
    <div class="holder__name">Daniel Moore</div>
    <div class="holder__role">Managing Director</div>
  </div>

  <svg class="decor-ring" width="250" height="250" viewBox="0 0 250 250" aria-hidden="true">
    <circle cx="125" cy="125" r="118" fill="none" stroke="var(--deep-mark)" stroke-width="6" opacity="0.7"/>
  </svg>

  <address class="address" style="font-style:normal">
    240 Cedar Ridge Road<br>
    Brandon, MS 39042
  </address>

  <ul class="contacts">
    <li>
      <svg viewBox="0 0 16 16" aria-hidden="true"><path fill="var(--accent-blue)" d="M3.3 1.2l2.3 2.6c.3.4.3.9 0 1.2L4.5 6.2c.8 2 2.6 3.8 4.6 4.6l1.2-1.1c.3-.3.8-.3 1.2 0l2.6 2.3c.4.3.4.9 0 1.3l-1.3 1.3c-.5.5-1.3.6-2 .4C6 13.7 2.3 10 1 5.1c-.2-.7 0-1.5.5-2l1.3-1.3c.1-.2.3-.6.5-.6z"/></svg>
      555.214.7390
    </li>
    <li>
      <svg viewBox="0 0 16 16" aria-hidden="true"><rect x="1.5" y="3.5" width="13" height="9" rx="1" fill="var(--accent-blue)"/><path d="M1.8 4l6.2 4.6L14.2 4" fill="none" stroke="var(--card-navy)" stroke-width="1.2"/></svg>
      hello@aureliscare.com
    </li>
    <li>
      <svg viewBox="0 0 16 16" aria-hidden="true"><circle cx="8" cy="8" r="7" fill="var(--accent-blue)"/><path d="M1 8h14M8 1c-2.5 2-2.5 12 0 14M8 1c2.5 2 2.5 12 0 14" fill="none" stroke="var(--card-navy)" stroke-width="1"/></svg>
      www.aureliscare.com
    </li>
  </ul>
</section>

<section class="card card--back">
  <svg class="decor-ring" width="50" height="50" viewBox="0 0 50 50" aria-hidden="true">
    <circle cx="25" cy="25" r="22" fill="none" stroke="var(--deep-mark)" stroke-width="4"/>
  </svg>
  <div class="brand-name">Aurelis Care Partners</div>
</section>

</body>
</html>
```